Construction Company

Design a clutter free business card, it can be double-sided utilizing the logo for VKM Ltd simple with all relevant contact information.

Please also a letterhead design to function for the purposes of invoicing, all mail requirements, with header to be distinctive while the footer ties page together and incorporates all necessary information.

For now, please use generic / dummy text and when a winner is selected, I will disclose the contact information.

Hi Designers! Please read the updated brief which includes the design of a business card and letterhead. Thank you!

```html
<!DOCTYPE html>
<html lang="en">
<head>
<meta charset="UTF-8">
<title>VKM Ltd Business Card</title>
<link href="https://fonts.googleapis.com/css2?family=Libre+Caslon+Text:wght@700&family=Arimo:wght@400&display=swap" rel="stylesheet">
<style>
  :root {
    --brand-blue: #00308f;
    --brand-gold: #b4921e;
    --card-white: #ffffff;
    --stage-grey: #a3a3a3;
    --text-dark: #333333;
    --rule-grey: #9a9a9a;
  }
  * { margin: 0; padding: 0; box-sizing: border-box; }
  html, body {
    width: 1200px;
    height: 1200px;
    overflow: hidden;
    background: var(--stage-grey);
  }
  .stage {
    position: relative;
    width: 1200px;
    height: 1200px;
  }
  .card {
    position: absolute;
    top: 305px;
    height: 598px;
  }
  .card-front {
    left: 201px;
    width: 372px;
    background: var(--brand-blue);
  }
  .card-back {
    left: 603px;
    width: 366px;
    background: var(--card-white);
  }
  .wordmark {
    position: absolute;
    left: 0;
    right: 0;
    display: flex;
    align-items: center;
    justify-content: center;
    gap: 10px;
    font-family: "Libre Caslon Text", "Times New Roman", serif;
    font-weight: 700;
    letter-spacing: 1px;
    white-space: nowrap;
  }
  .wordmark-dot {
    width: 14px;
    height: 14px;
    border-radius: 50%;
    background: var(--brand-gold);
    flex: none;
  }
  .card-front .wordmark {
    top: 262px;
    font-size: 54px;
    color: var(--card-white);
  }
  .card-back .wordmark {
    top: 132px;
    font-size: 52px;
    color: var(--brand-blue);
  }
  .contact-block {
    position: absolute;
    top: 310px;
    left: 0;
    right: 0;
    text-align: center;
    font-family: "Arimo", Arial, sans-serif;
    color: var(--text-dark);
  }
  .person-name {
    font-family: "Libre Caslon Text", "Times New Roman", serif;
    font-weight: 700;
    font-size: 20px;
    color: var(--brand-blue);
    letter-spacing: 0.5px;
    line-height: 1;
  }
  .person-role {
    font-size: 17px;
    margin-top: 3px;
  }
  .icon-row {
    display: flex;
    align-items: center;
    justify-content: center;
    gap: 4px;
    margin-top: 14px;
  }
  .icon-row .rule {
    width: 36px;
    height: 1px;
    background: var(--rule-grey);
    margin: 0 2px;
  }
  .icon-tile {
    width: 25px;
    height: 25px;
    border-radius: 3px;
    background: var(--brand-blue);
    display: flex;
    align-items: center;
    justify-content: center;
  }
  .contact-lines {
    margin-top: 10px;
    font-size: 17px;
    line-height: 21.7px;
  }
  .contact-lines .accent { color: var(--brand-blue); }
  .divider {
    width: 195px;
    height: 1px;
    background: var(--rule-grey);
    margin: 10px auto 12px;
  }
  .address {
    font-size: 17px;
    line-height: 21.7px;
  }
</style>
</head>
<body>
<main class="stage">
  <section class="card card-front">
    <div class="wordmark"><span class="wordmark-dot"></span>VKM Ltd</div>
  </section>

  <section class="card card-back">
    <div class="wordmark"><span class="wordmark-dot"></span>VKM Ltd</div>

    <div class="contact-block">
      <div class="person-name">JONATHAN SMITH</div>
      <div class="person-role">Managing Director</div>

      <div class="icon-row">
        <span class="rule"></span>
        <span class="icon-tile" aria-label="Phone">
          <svg width="15" height="15" viewBox="0 0 16 16"><path d="M2 6c0-2 2-3 6-3s6 1 6 3v1h-3V6H5v1H2z M4 8h8l1 5H3z" fill="#fff"/></svg>
        </span>
        <span class="icon-tile" aria-label="Mobile">
          <svg width="15" height="15" viewBox="0 0 16 16"><rect x="4.5" y="1.5" width="7" height="13" rx="1.2" fill="none" stroke="#fff" stroke-width="1.4"/><circle cx="8" cy="12.3" r="0.8" fill="#fff"/></svg>
        </span>
        <span class="icon-tile" aria-label="Email">
          <svg width="15" height="15" viewBox="0 0 16 16"><rect x="1.5" y="3.5" width="13" height="9" fill="none" stroke="#fff" stroke-width="1.3"/><path d="M1.5 3.5 8 9l6.5-5.5M1.5 12.5 6 8M14.5 12.5 10 8" fill="none" stroke="#fff" stroke-width="1.1"/></svg>
        </span>
        <span class="icon-tile" aria-label="Website">
          <svg width="15" height="15" viewBox="0 0 16 16"><circle cx="8" cy="8" r="6" fill="none" stroke="#fff" stroke-width="1.4"/><path d="M2 8h12M8 2c-2.5 3-2.5 9 0 12M8 2c2.5 3 2.5 9 0 12" fill="none" stroke="#fff" stroke-width="1"/></svg>
        </span>
        <span class="rule"></span>
      </div>

      <div class="contact-lines">
        <div>044-123 456 789</div>
        <div>044-123 456 789</div>
        <div>info@webname.com</div>
        <div>www.<span class="accent">websitename</span>.com</div>
      </div>

      <div class="divider"></div>

      <div class="address">
        <div>421, Address line here</div>
        <div>45452,Country Name</div>
      </div>
    </div>
  </section>
</main>
</body>
</html>
```